Business card for a Exhibition booth fabrication company

Hi. My company would like to change our corporate name card. We are an events and Exhibition stand builder company. We would like our corporate name card to resonate what we do. I need someone to create something unique that relates to the industry that I am in. The graphic designer should be creative to incorporate the elements of my industry and try to blend in well in the design of the card. Our aim is to ensure that we are unique and our card can look different from our competitors.
Updates

Target Market(s)

Marketing and events manager from all companies

Contact Information for Business Card

The business card should have the following details:
Name
Job Title
Email
Website

Colors

Designer to choose colors to be used in the design.

Requirements
Must have
• The card must be look something that is relevant to the service that I am providing. My website is: www.velmora-buildworks.com
• You can see my website to get more information on what service that I am doing
Nice to have
• On the back of my card, I would like to have a globe image with the incorporation of my company logo. This is to indicate that my services can be done in any part of the world.

```html
<!DOCTYPE html>
<html lang="en">
<head>
<meta charset="utf-8">
<title>Velmora Buildworks – Business Card</title>
<link rel="stylesheet" href="https://fonts.googleapis.com/css2?family=Montserrat:wght@600&family=PT+Serif:wght@400&display=swap">
<style>
  :root {
    --page: #d9dbde;
    --card-white: #ffffff;
    --charcoal: #2e2d2e;
    --charcoal-light: #3d3b3c;
    --brand-red: #e21f26;
    --deep-red: #7d0c10;
    --ink: #2b2b2b;
    --map-grey: #cfcfcf;
    --text-light: #f2f2f2;
  }
  * { margin: 0; padding: 0; box-sizing: border-box; }
  html, body { width: 1200px; height: 1200px; overflow: hidden; background: var(--page); }
  .canvas { position: relative; width: 1200px; height: 1200px; }

  .card {
    position: absolute;
    left: 150px;
    width: 900px;
    height: 514px;
    background: var(--card-white);
    overflow: hidden;
    box-shadow: 0 6px 18px rgba(0,0,0,0.18);
  }
  .card--front { top: 60px; }
  .card--back { top: 626px; }

  .card-shapes { position: absolute; inset: 0; width: 100%; height: 100%; }

  .holder { position: absolute; left: 70px; top: 62px; }
  .holder-name {
    font-family: "Montserrat", sans-serif;
    font-weight: 600;
    font-size: 34px;
    letter-spacing: 1px;
    color: var(--text-light);
  }
  .holder-name .first { color: var(--brand-red); }
  .holder-title {
    font-family: "PT Serif", serif;
    font-size: 21px;
    color: var(--text-light);
    margin-top: 4px;
  }
  .holder-rule {
    position: absolute; left: 70px; top: 176px;
    width: 330px; height: 3px; background: var(--brand-red);
  }

  .contact { position: absolute; left: 52px; top: 266px; list-style: none; }
  .contact li {
    display: flex; align-items: center; gap: 14px;
    font-family: "PT Serif", serif;
    font-size: 21px;
    color: var(--text-light);
    margin-bottom: 14px;
  }
  .contact svg { width: 22px; height: 22px; flex: none; }

  .brand {
    position: absolute;
    display: flex; align-items: center; gap: 16px;
  }
  .brand-dot { width: 26px; height: 26px; border-radius: 50%; background: var(--brand-red); }
  .brand-name {
    font-family: "Montserrat", sans-serif;
    font-weight: 600;
    letter-spacing: 3px;
    color: var(--ink);
  }
  .card--front .brand { left: 540px; top: 230px; }
  .card--front .brand-name { font-size: 24px; }

  .world-map {
    position: absolute; left: 180px; top: 70px; width: 560px; height: 380px;
    border-radius: 45%;
    background: radial-gradient(ellipse at 50% 45%, var(--map-grey) 0%, rgba(207,207,207,0.55) 45%, rgba(255,255,255,0) 72%);
  }
  .card--back .brand { left: 0; right: 0; top: 232px; justify-content: center; }
  .card--back .brand-name { font-size: 34px; }
</style>
</head>
<body>
<main class="canvas">

  <section class="card card--front" aria-label="Business card front">
    <svg class="card-shapes" viewBox="0 0 900 514" aria-hidden="true">
      <polygon points="0,0 560,0 400,440 0,440" fill="var(--charcoal)"/>
      <polygon points="560,0 720,0 515,120" fill="var(--brand-red)"/>
      <rect x="0" y="410" width="400" height="104" fill="var(--charcoal)"/>
      <rect x="0" y="410" width="215" height="104" fill="var(--charcoal-light)"/>
      <rect x="225" y="410" width="150" height="104" fill="var(--deep-red)"/>
      <rect x="385" y="420" width="440" height="60" fill="var(--brand-red)"/>
    </svg>

    <div class="holder">
      <h1 class="holder-name"><span class="first">ARLO</span> PENN</h1>
      <p class="holder-title">Director</p>
    </div>
    <div class="holder-rule"></div>

    <ul class="contact">
      <li>
        <svg viewBox="0 0 24 24" aria-hidden="true"><rect x="2" y="5" width="20" height="14" fill="var(--brand-red)"/><polyline points="2,5 12,13 22,5" fill="none" stroke="var(--charcoal)" stroke-width="2"/></svg>
        username@velmora-buildworks.com
      </li>
      <li>
        <svg viewBox="0 0 24 24" aria-hidden="true"><circle cx="12" cy="12" r="10" fill="none" stroke="var(--brand-red)" stroke-width="2"/><ellipse cx="12" cy="12" rx="4" ry="10" fill="none" stroke="var(--brand-red)" stroke-width="2"/><line x1="2" y1="12" x2="22" y2="12" stroke="var(--brand-red)" stroke-width="2"/></svg>
        www.velmora-buildworks.com
      </li>
    </ul>

    <div class="brand">
      <span class="brand-dot"></span>
      <span class="brand-name">VELMORA BUILDWORKS</span>
    </div>
  </section>

  <section class="card card--back" aria-label="Business card back">
    <div class="world-map" role="img" aria-label="Faint grey world map spanning the card"></div>
    <div class="brand">
      <span class="brand-dot"></span>
      <span class="brand-name">VELMORA BUILDWORKS</span>
    </div>
  </section>

</main>
</body>
</html>
```